Software Development Consulting Company Needs Business Card Design

We need a new business card design for our consultants at Kestrel Works (kestrelworks.example). We are a small firm that provides high-end software development and methodology consulting to medium to large enterprise IT organizations.

Our logo uses Futura for the font and we would like to stick with navy blue and canary yellow for the logo colors. Attached are normal and reversed versions of our logos in illustrator format.
Updates

Hi Everyone, Thank yo very much for your amazing design ideas. I have created a poll for this project and our employees will be voting on the design they wish to use. We will be making a decision this Wednesday (October 22nd). Thanks again, Dale Hartwick

Industry/Entity Type

Business

```html
<!DOCTYPE html>
<html lang="en">
<head>
<meta charset="utf-8">
<title>Kestrel Works – Business Card</title>
<link rel="stylesheet" href="https://fonts.googleapis.com/css2?family=Open+Sans:wght@400;600;700&display=swap">
<style>
  :root {
    --navy: #1b4a6e;
    --canary: #f5e50f;
    --ink: #3a3a3a;
    --muted: #666666;
    --grey-rule: #c9c9c9;
    --paper: #ffffff;
    --backdrop: #e9e9ee;
  }
  * { box-sizing: border-box; margin: 0; padding: 0; }
  html, body {
    width: 1200px; height: 980px; overflow: hidden;
    background: var(--backdrop);
    font-family: "Open Sans", Arial, sans-serif;
  }
  .canvas { position: relative; width: 1200px; height: 980px; }

  .card {
    position: absolute; left: 250px; width: 700px; height: 400px;
    background: var(--paper); border-radius: 22px; overflow: hidden;
    box-shadow: 0 6px 20px rgba(0,0,0,.12);
  }
  .card--front { top: 60px; }
  .card--back  { top: 520px; }

  /* Brand lockup: name with one plain circle */
  .brand {
    position: absolute; display: flex; align-items: center; gap: 12px;
    color: var(--navy); font-weight: 600; letter-spacing: 5px; white-space: nowrap;
  }
  .card--front .brand { left: 40px; top: 110px; font-size: 27px; }
  .brand__dot { width: 14px; height: 14px; border-radius: 50%; background: var(--canary); flex: none; }

  .divider {
    position: absolute; left: 372px; top: 30px; width: 2px; height: 220px;
    background: linear-gradient(to bottom, transparent, var(--grey-rule) 30%, var(--grey-rule) 70%, transparent);
  }

  .contact { position: absolute; left: 400px; top: 46px; color: var(--ink); }
  .contact__name { color: var(--navy); font-weight: 700; font-size: 26px; letter-spacing: -.3px; }
  .contact__title { font-size: 17px; color: var(--muted); margin-bottom: 18px; }
  .contact__line { display: flex; align-items: center; gap: 8px; font-size: 17px; line-height: 28px; white-space: nowrap; }
  .contact__line svg { width: 17px; height: 17px; flex: none; }

  .band {
    position: absolute; left: 0; right: 0; top: 262px; height: 96px;
    border-top: 3px solid var(--canary); border-bottom: 3px solid var(--canary);
    padding: 9px 0; background: var(--paper);
  }
  .band__fill {
    height: 100%; background: var(--navy); color: var(--paper);
    display: flex; align-items: center; padding-left: 44px;
    font-size: 20px; letter-spacing: 3px;
  }

  .card--back .brand { right: 60px; top: 140px; font-size: 34px; }
  .back__url {
    position: absolute; left: 44px; bottom: 54px;
    color: var(--ink); font-size: 21px; letter-spacing: 4px;
  }
</style>
</head>
<body>
<main class="canvas">

  <section class="card card--front" aria-label="Business card front">
    <div class="brand"><span class="brand__dot"></span>KESTREL WORKS</div>
    <div class="divider"></div>

    <div class="contact">
      <p class="contact__name">Dale Hartwick</p>
      <p class="contact__title">Title</p>
      <p class="contact__line">
        <svg viewBox="0 0 20 20" aria-hidden="true"><circle cx="10" cy="10" r="8.5" fill="none" stroke="var(--ink)" stroke-width="1.6"/><path d="M7 5.5l2 2-1 1.3c.6 1.4 1.6 2.4 3 3l1.3-1 2 2-1.3 1.5c-3.2-.5-6-3.3-6.5-6.5z" fill="var(--ink)"/></svg>
        555-014-2276
      </p>
      <p class="contact__line">
        <svg viewBox="0 0 20 20" aria-hidden="true"><rect x="1.5" y="4" width="17" height="12" rx="1.5" fill="var(--navy)"/><path d="M2.5 5l7.5 6 7.5-6" fill="none" stroke="#fff" stroke-width="1.5"/></svg>
        info@kestrelworks.example
      </p>
      <p class="contact__line">Ridgefield + Maple Falls, IL</p>
    </div>

    <div class="band"><div class="band__fill">www.kestrelworks.example</div></div>
  </section>

  <section class="card card--back" aria-label="Business card back">
    <div class="brand"><span class="brand__dot"></span>KESTREL WORKS</div>
    <p class="back__url">www.kestrelworks.example</p>
  </section>

</main>
</body>
</html>
```